Diverse, up-scale salon needs eye-catching, unique business cards.

We are looking for a unique business card design for our stylist but that can also be multi functional and used for appointment reminder and referrals. I will need a design in a format that I can modify names and titles going forward. In the past we have had a dark background with the logo on one side, and stylist and contact information on the other but we are open to all ideas. I have included our mission statement as well as branded colors below. The statement doesn't need to go on the card, it's just a reference for target market. We need space for the stylists name, title, instagram handle and then the salons phone number, website and address. I am also open to adding a spot for a qr code linked to the stylist instagram or the salon booking link.

primary brand colors:
#333333 #233415 #36502a #93874a #000000
Mission statement:
Vessolin Hair Studio, a high-end salon located in the lively Downtown Farmington, Michigan, is committed to providing exceptional services in a welcoming and relaxed environment to meet the needs of our diverse clientele.
Our salon specializes in contemporary custom haircuts, coloring, extensions, and barbering and beard grooming services. Our team of skilled stylists is passionate and inventive in their hair styling techniques. At the heart of our salon are values centered on quality, innovation, creativity, and above all, comfort. These core values are evident in every appointment across our customizable array of services.
Our goal is to establish a benchmark for exceptional hair care for every human.
Website: www.vessolinhairstudio.example
instagram: @vessolinhairstudio
address: 41782 Pelham Crest Rd, Farmington MI
phone: 248-613-4087

Industry/Entity Type

Hair Salon

Contact Information for Business Card

Stylist name, title, phone, instagram, website, address, (optional qr code)

Requirements
Should not have
• Does not need mission statement on the card.

```html
<!DOCTYPE html>
<html lang="en">
<head>
<meta charset="utf-8">
<title>Vessolin Hair Studio – Business Card</title>
<link href="https://fonts.googleapis.com/css2?family=Montserrat:wght@400;600&display=swap" rel="stylesheet">
<style>
  :root {
    --backdrop: #3a3a3a;
    --card-light: #ffffff;
    --card-dark: #141414;
    --ink: #111111;
    --ink-soft: #222222;
    --emboss: #2a2a2a;
  }
  * { margin: 0; padding: 0; box-sizing: border-box; }
  html, body { width: 1200px; height: 1059px; overflow: hidden; }
  body {
    background: var(--backdrop);
    font-family: "Montserrat", Arial, sans-serif;
    position: relative;
  }
  .card {
    position: absolute;
    border-radius: 18px;
    overflow: hidden;
  }
  .card--front { left: 256px; top: 100px; width: 688px; height: 391px; background: var(--card-light); }
  .card--back  { left: 253px; top: 537px; width: 694px; height: 394px; background: var(--card-dark); }

  .brand-mark {
    position: absolute;
    border-radius: 50%;
    display: flex; align-items: center; justify-content: center;
    text-align: center;
    font-weight: 600;
    text-transform: uppercase;
    letter-spacing: 2px;
    line-height: 1.35;
  }
  .card--front .brand-mark {
    left: 94px; top: 91px; width: 206px; height: 206px;
    border: 2.5px solid var(--ink);
    color: var(--ink);
    font-size: 17px;
  }
  .card--back .brand-mark {
    left: 218px; top: 88px; width: 222px; height: 222px;
    border: 2.5px solid var(--emboss);
    color: var(--emboss);
    font-size: 19px;
  }

  .divider {
    position: absolute; left: 344px; top: 91px;
    width: 1.5px; height: 209px; background: var(--ink);
  }
  .details { position: absolute; left: 382px; top: 86px; color: var(--ink-soft); }
  .stylist-name { font-size: 28px; font-weight: 600; letter-spacing: 1px; color: var(--ink); line-height: 1.2; }
  .stylist-title { font-size: 15px; letter-spacing: 0.6px; margin-top: 2px; }
  .address { font-size: 15px; line-height: 20px; margin-top: 22px; letter-spacing: 0.3px; }
  .contacts { list-style: none; margin-top: 22px; }
  .contacts li {
    display: flex; align-items: center; gap: 8px;
    font-size: 15px; line-height: 22px; letter-spacing: 0.3px;
  }
  .contacts svg { width: 12px; height: 12px; flex: none; }
</style>
</head>
<body>
  <section class="card card--front">
    <div class="brand-mark">Vessolin<br>Hair Studio</div>
    <div class="divider"></div>
    <div class="details">
      <h1 class="stylist-name">DARREN COLWICK</h1>
      <p class="stylist-title">MANAGER</p>
      <p class="address">41782 Pelham Crest<br>Rd, Farmington MI</p>
      <ul class="contacts">
        <li>
          <svg viewBox="0 0 12 12" aria-hidden="true"><path d="M2.5 1 L4.5 1 L5.3 3.5 L4 4.5 Q5 7 7.5 8 L8.5 6.7 L11 7.5 L11 9.5 Q10.5 11 9 11 Q1 10 1 2.5 Q1 1 2.5 1 Z" fill="#111"/></svg>
          248-613-4087
        </li>
        <li>
          <svg viewBox="0 0 12 12" aria-hidden="true"><rect x="0.5" y="2" width="11" height="8" rx="1" fill="#111"/><path d="M1 2.8 L6 6.6 L11 2.8" stroke="#fff" stroke-width="1" fill="none"/></svg>
          info@vessolinhairstudio.example
        </li>
        <li>
          <svg viewBox="0 0 12 12" aria-hidden="true" fill="none" stroke="#111" stroke-width="1"><circle cx="6" cy="6" r="5.2"/><ellipse cx="6" cy="6" rx="2.3" ry="5.2"/><path d="M0.8 6 H11.2 M1.6 3.4 H10.4 M1.6 8.6 H10.4"/></svg>
          www.vessolinhairstudio.example
        </li>
        <li>
          <svg viewBox="0 0 12 12" aria-hidden="true"><circle cx="6" cy="6" r="5" fill="none" stroke="#111" stroke-width="1.3"/></svg>
          @vessolinhairstudio
        </li>
      </ul>
    </div>
  </section>

  <section class="card card--back">
    <div class="brand-mark">Vessolin<br>Hair Studio</div>
  </section>
</body>
</html>
```